Brightmoor - a website to encourage people to spend time in nature

I have a squarespace site with some content on it but the squarespace template doesn't completely suit my needs, I keep fiddling with the template but actually I need some professional help to get it looking the way I want and with the right 'mood'.
The website is for "Brightmoor" - it will be a blog where I write about the importance of nature for good health. I also want to use the website to market services such as outdoor coaching, retreats and walking workshops.
This has been in my head for a LONG time and I currently only use instagram for micro-blogs but it's time for me to get this moving. I've previously engaged other designers on branding for it but they just didn't get it quite the way that I wanted it and I wasn't completely happy with the results. It's been a process for me as to what I want but in the meantime I just didn't come back to the design aspect of it now. I'm looking for a designer who understands the purpose of the website, the ethos and can help me realise this into a design that's clean, clear and simple.

Please note that I have a domain (brightmoor.org) and a lot of content drafted on squarespace already. I have published it with password protection - password is brightmoor2020 - it still has some of the original template on it, but does have some content. Don't take it as anything to follow in particular, i am looking for fresh eyes and fresh ideas.

Target Market(s)

There are three main groups that I want to target - people who are suffering from stress and anxiety, people who treat them and parents who want to get their kids outside (thereby preventing stress and anxiety)

Contact Information for Business Card

Joan Petrie
Brightmoor
Telephone +44 7700 900417
brightmoor@mailvane.com

Logo Text

Brightmoor - if that. I have an idea that the logo should have a leaf on it somewhere, or maybe just be a leaf.

Coding

Coded - Design and coding required

Number of Pages Required

5+ page

Font styles to use
Serif
Sans Serif

Colors
add136
33b8a4
34a6d7
3377b5

Requirements
Must have
• Space for lots of images. The ability for me to edit the pages if I need to. Be user friendly. Look beautiful.
• For an idea of the images I use and the content I'm interested in writing about have a look at @brightmoor on instagram.
• That pop up about cookies so I am complying with data laws.
Should not have
• Must not be too 'busy' I'd like to avoid too much movement.

```html
<!DOCTYPE html>
<html lang="en">
<head>
<meta charset="utf-8">
<title>Brightmoor</title>
<link rel="stylesheet" href="https://fonts.googleapis.com/css2?family=Roboto:wght@400;500;700&display=swap">
<style>
:root{
  --teal:#2aab91;
  --teal-btn:#33b8a4;
  --blue:#2862a8;
  --sky:#34a6d7;
  --ink:#222;
  --muted:#444;
  --white:#fff;
  --black:#050505;
}
*{box-sizing:border-box;margin:0;padding:0}
html,body{width:1200px;height:2204px;overflow:hidden}
body{font-family:"Roboto",Arial,sans-serif;color:var(--white);position:relative;background:var(--white)}
.abs{position:absolute}

.cookie-bar{left:0;top:0;width:1200px;height:38px;background:var(--black);display:flex;align-items:center;justify-content:center;gap:6px;font-size:11px}
.cookie-bar .label{color:var(--teal-btn);font-size:13px}
.cookie-bar .msg{color:#ddd;margin-right:22px}
.cookie-btn{font-size:11px;padding:4px 8px;border:0}
.cookie-btn.accept{background:var(--teal);color:var(--white)}
.cookie-btn.close{background:var(--white);color:var(--ink)}

.hero{left:0;top:38px;width:1200px;height:625px;
  background:radial-gradient(ellipse at 55% 40%,#5a6a44 0%,#3a4a2c 35%,#1f2a18 75%,#141c10 100%)}
.hero-shade{left:0;top:38px;width:1200px;height:625px;background:linear-gradient(180deg,rgba(0,0,0,.25),rgba(0,0,0,.1) 50%,rgba(0,0,0,.3))}

.brand{display:flex;align-items:center;gap:8px}
.brand .dot{width:22px;height:22px;border-radius:50%;background:var(--teal)}
.brand .name{font-size:26px;font-weight:500;letter-spacing:.5px}
.header-brand{left:172px;top:86px}
.header-brand .name{color:var(--white)}

.nav{left:573px;top:90px;display:flex;gap:35px;font-size:15px;color:#eee}
.nav .active{color:var(--teal-btn);border-bottom:2px solid var(--teal-btn);padding-bottom:3px}
.cta{left:939px;top:84px;width:89px;height:33px;background:linear-gradient(90deg,var(--teal-btn),var(--sky));font-size:12px;font-weight:500;display:flex;align-items:center;justify-content:center}

.hero-title{left:0;top:306px;width:1200px;text-align:center;font-size:35px;font-weight:500;line-height:42px;text-transform:uppercase}
.hero-link{left:0;top:404px;width:1200px;text-align:center;font-size:19px;font-weight:500}
.hero-link span{border-bottom:2px solid var(--white);padding-bottom:1px}

.services{left:0;top:663px;width:1200px;height:553px;background:var(--teal)}
.section-title{font-size:41px;font-weight:700}
.services-title{left:172px;top:697px}
.card{top:774px;width:412px;height:263px;display:flex;align-items:center;justify-content:center;font-size:23px;font-weight:700}
.card.walking{left:172px;background:linear-gradient(180deg,#8c9090 0%,#6d6a5e 30%,#4d3a2c 55%,#3f4a2a 100%)}
.card.skytime{left:615px;background:linear-gradient(180deg,#8e9496 0%,#80878c 55%,#5f6b72 75%,#46545c 100%)}
.services-text{left:172px;top:1060px;font-size:18px;line-height:24px}
.outline-btn{height:38px;border:2px solid var(--white);font-size:14px;font-weight:500;display:flex;align-items:center;justify-content:center}
.services-btn{left:172px;top:1128px;width:119px}

.about{left:0;top:1216px;width:1200px;height:368px;background:var(--blue)}
.about-title{left:172px;top:1295px}
.about-text{left:172px;top:1361px;width:540px;font-size:18px;line-height:31px}
.about-side{left:802px;top:1335px;width:250px;font-size:13px;line-height:24px}
.about-btn{left:802px;top:1428px;width:119px}

.newsletter{left:0;top:1584px;width:1200px;height:423px;
  background:linear-gradient(180deg,#3b4a34 0%,#4d5c3a 35%,#3e4a36 62%,#4a3a86 78%,#3a2c6e 100%)}
.news-title{left:0;top:1688px;width:1200px;text-align:center;font-size:42px;font-weight:700}
.news-text{left:0;top:1745px;width:1200px;text-align:center;font-size:14px;line-height:22px}
.field{top:1815px;width:202px;height:49px;background:var(--white);color:#888;font-size:13px;padding-left:13px;display:flex;align-items:center}
.signup{left:857px;top:1815px;width:117px;height:49px;background:linear-gradient(90deg,var(--teal-btn),var(--sky));font-size:15px;font-weight:500;display:flex;align-items:center;justify-content:center}

.footer-brand{left:172px;top:2060px}
.footer-brand .name{color:var(--teal)}
.copyright{left:171px;top:2124px;font-size:13px;color:var(--ink)}
.footer-col{font-size:14px;line-height:24px;color:var(--muted)}
.address{left:508px;top:2071px}
.footer-links{left:752px;top:2071px}
.social{left:904px;top:2085px;display:flex;gap:18px}
.social span{width:15px;height:15px;border-radius:50%;background:#555}
</style>
</head>
<body>
<div class="abs cookie-bar">
  <span class="label">Cookies:</span>
  <span class="msg">Lorem ipsum dolor sit amet consectetur adipiscing elit sed do eiusmoet consectetur adipiscing elit sed do eiusmod.</span>
  <span class="cookie-btn accept">Accept</span>
  <span class="cookie-btn close">Close</span>
</div>

<div class="abs hero" role="img" aria-label="Photograph of a shaded forest path between tall trees"></div>
<div class="abs hero-shade"></div>
<div class="abs brand header-brand"><span class="dot"></span><span class="name">Brightmoor</span></div>
<nav class="abs nav">
  <span class="active">Home</span><span>About</span><span>Blog</span><span>Gallery</span><span>Contact</span>
</nav>
<div class="abs cta">Get Started</div>
<h1 class="abs hero-title">The practice of feeling better<br>by spending time in nature.</h1>
<div class="abs hero-link"><span>Tell Me More</span></div>

<section class="abs services"></section>
<h2 class="abs section-title services-title">What We Do</h2>
<div class="abs card walking" role="img" aria-label="Photograph of a walker on a boardwalk through moorland">Walking Initiative</div>
<div class="abs card skytime" role="img" aria-label="Photograph of a child looking out to sea">Skytime over Screentime</div>
<p class="abs services-text">Our aim is to help people connect with nature as a means to feeling better.<br>We do this in a number of ways.</p>
<div class="abs outline-btn services-btn">Read More</div>

<section class="abs about"></section>
<h2 class="abs section-title about-title">About Brightmoor</h2>
<p class="abs about-text">Brightmoor Walking is an initiative aimed at getting people back into nature in the most gentlest of ways - by taking a walk with friends in the great outdoors. The concept is simple - schedule a walk outside, once a week with two or three other people.</p>
<p class="abs about-side">Our aim is to help people connect<br>with nature as a means to feeling better.<br>We do this in a number of ways.</p>
<div class="abs outline-btn about-btn">Read More</div>

<section class="abs newsletter" role="img" aria-label="Photograph of a woodland with bluebells carpeting the ground"></section>
<h2 class="abs news-title">Subscribe to Our Newsletter</h2>
<p class="abs news-text">Lorem ipsum dolor sit amet, consectetur adipiscing elit, sed do eiusmod<br>tempor incididunt ut labore et dolore magna aliqua enim</p>
<div class="abs field" style="left:226px">First Name</div>
<div class="abs field" style="left:436px">Last Name</div>
<div class="abs field" style="left:646px">Email</div>
<div class="abs signup">Sign Up</div>

<div class="abs brand footer-brand"><span class="dot"></span><span class="name">Brightmoor</span></div>
<p class="abs copyright">Copyright 2020 All Rights Reserved</p>
<div class="abs footer-col address">14 Heather Row<br>Ambleside, LA22<br>+44 7700 900417</div>
<div class="abs footer-col footer-links">About<br>Blog<br>Gallery<br>Contact</div>
<div class="abs social" aria-label="Social links"><span></span><span></span><span></span><span></span></div>
</body>
</html>
```